KM Guild of Realtors

We are working with the Kestrel Meadow Guild of Realtors.

Some sites to use for content/competitors and inspiration:
https://www.plv.realtor
https://brimforthagent.com
https://qxagents.com
https://www.corvalhomeland.com
https://www.gwobel.com

Thank you for taking the time to consider designing a website for us. We are web developers based in Stockton, CA, USA. Most of our projects go through the same process. Understanding this process may help you win a project with us. We custom-code all of our websites in-house. We don’t have any requirements as to what tools you use for your design, but we prefer Figma files. For any design that we label as four-stars, we send it to the client for review. The client picks the final design they want us to use. Once we complete this process, we will continue to show additional clients all the four-star sites and purchase them later. Your designs will have multiple chances to sell. For better chances of success, we ask that you follow these guidelines.

IMAGES:
If you use any images or icons in the design, we ask that you have a link to the asset so we can purchase the image/icon. Most of the designs we submit do not have the customer’s images on them unless they have some great images. Be creative; show us the feeling you are trying to portray with your image choices. Use any royalty-free site you choose. We subscribe to Velkor and mainly use their images, but we can purchase images outside of Velkor.

PLEASE NOTE: we will not submit designs to clients with watermarks on the images.

FONTS:
We ask that you identify the fonts used in the design. This can be done in a message if you want. We typically use Zinthra Fonts and Velkor Fonts.

CONTENT:
We're always open to different content and ideas. We often submit designs with stock images so the client can see our vision. We typically take pictures after the website launch to use their images with our vision. Lorem Ipsum is fine for paragraphs, but we ask that you write the headers in correct English. We want to be able to show the vision and identify the sections of the website.

INSPIRATION:
We typically add a couple of links in the brief of websites we like to help you get started in your design.

REVISIONS:
We do not often ask for revisions of the designs unless we see something in the design that may not appeal to the client. If there are slight changes that we want to make, we do that in the development process.

FEEDBACK:
We rarely give feedback on designs during the design process. We are working on many website projects and do not have the time to provide feedback. We usually respond if your request is well thought out and asks specific questions, but a note asking “feedback, please” usually goes unanswered

```html
<!DOCTYPE html>
<html lang="en">
<head>
<meta charset="utf-8">
<title>KM Guild of Realtors</title>
<link href="https://fonts.googleapis.com/css2?family=Poppins:wght@400;500;600;700;800&display=swap" rel="stylesheet">
<style>
:root{
  --navy:#1767a8;
  --sky:#1fa8d0;
  --yellow:#ffd51a;
  --ink:#2b2b2b;
  --muted:#707070;
  --paper:#ffffff;
  --mist:#efefef;
  --team:#1b6fb0;
  --night:#151515;
}
*{margin:0;padding:0;box-sizing:border-box}
html,body{width:1200px;height:4059px;overflow:hidden}
body{font-family:"Poppins",sans-serif;color:var(--ink);background:var(--paper);position:relative}
.abs{position:absolute}
.btn{position:absolute;background:var(--yellow);color:#1c1c1c;font-weight:600;font-size:15px;display:flex;align-items:center;justify-content:center}
.brand{display:flex;align-items:center;gap:8px;font-weight:700;color:var(--navy);letter-spacing:1px}
.brand .dot{width:14px;height:14px;background:var(--yellow)}
.tagline{font-size:11px;color:var(--navy);letter-spacing:.3px}
.para{font-size:14px;line-height:26px;color:var(--muted)}

/* hero */
.hero{position:absolute;left:0;top:0;width:1200px;height:651px;background:linear-gradient(90deg,#eef0f1 0%,#e6e8ea 45%,#dcdfe2 100%)}
.hero-photo{position:absolute;left:470px;top:0;width:730px;height:651px;background:linear-gradient(180deg,#eceeef 0%,#d9dcdf 55%,#c9cdd1 100%)}
.nav{position:absolute;top:44px;left:531px;display:flex;gap:51px;font-size:15px;color:#333}
.hero h1{position:absolute;left:114px;top:350px;font-size:36px;line-height:57px;font-weight:700;color:#2b2b2b}
.hero h1 span{color:var(--sky)}
.band{position:absolute;left:0;width:1200px;height:10px;background:var(--sky)}

/* about */
.about h2,.center-title{font-size:38px;font-weight:700;color:var(--navy)}
.center-title{position:absolute;width:1200px;text-align:center}
.center-title span{color:var(--sky)}
.diamond{position:absolute;clip-path:polygon(50% 0,100% 50%,50% 100%,0 50%)}

/* services */
.services{position:absolute;left:0;top:1383px;width:1200px;height:514px;background:linear-gradient(135deg,#f4f4f4,#e9e9e9)}
.service{position:absolute;top:155px;width:200px;text-align:center}
.service .frame{margin:0 auto;width:170px;height:200px;border:12px solid var(--navy);border-bottom-color:var(--sky);border-right-color:var(--sky);display:flex;align-items:center;justify-content:center;background:transparent}
.service .icon{width:78px;height:78px;border-radius:50%;background:#ffe574}
.service p{margin-top:20px;font-size:26px;font-weight:500;color:#2b2b2b}

/* team */
.team{position:absolute;left:0;top:2531px;width:1200px;height:490px;background:linear-gradient(90deg,#1d6aa8,#1b72b4 50%,#1a6cac)}
.member{position:absolute;top:147px;width:230px;text-align:center;color:#fff}
.member .photo{width:230px;height:224px}
.member h3{margin-top:14px;font-size:16px;font-weight:700}
.member p{font-size:13px}

/* contact */
.field{position:absolute;background:#fff;box-shadow:0 2px 12px rgba(0,0,0,.09);font-size:13px;color:#555;padding:24px 22px 0}

/* footer */
.footer{position:absolute;left:0;top:3698px;width:1200px;height:361px;background:var(--night);color:#fff}
.footer h4{position:absolute;top:80px;font-size:20px;font-weight:600}
.footer ul{position:absolute;top:122px;list-style:none;font-size:14px;line-height:26px}
.footer li::before{content:"»";margin-right:10px}
.social{position:absolute;top:227px;width:38px;height:38px;border-radius:50%;background:#fff}
.contact-line{position:absolute;font-size:14px;line-height:24px;display:flex;gap:10px}
</style>
</head>
<body>

<header class="hero">
  <div class="hero-photo" role="img" aria-label="Photo of a realtor pointing out a bright empty room to a smiling couple"></div>
  <div class="abs" style="left:110px;top:30px">
    <div class="brand" style="font-size:38px"><span>KMGR</span><span class="dot"></span></div>
    <div class="tagline">WE EMPOWER • WE EDUCATE • WE CONNECT</div>
  </div>
  <nav class="nav"><span>Home</span><span>About Us</span><span>Services</span><span>Blog</span><span>Contact us</span></nav>
  <svg class="abs" style="left:1055px;top:42px" width="26" height="26" viewBox="0 0 26 26"><circle cx="11" cy="11" r="8" fill="none" stroke="#333" stroke-width="2"/><line x1="17" y1="17" x2="24" y2="24" stroke="#333" stroke-width="2"/></svg>
  <div class="brand abs" style="left:113px;top:255px;font-size:56px"><span>KMGR</span><span class="dot" style="width:20px;height:20px"></span></div>
  <h1>THE VOICE OF REAL<br>ESTATE IN <span>KMGR</span></h1>
  <div class="btn" style="left:115px;top:487px;width:130px;height:48px">Get started</div>
</header>

<div class="band" style="top:651px"></div>
<svg class="abs" style="left:545px;top:651px" width="110" height="60" viewBox="0 0 110 60"><polygon points="0,0 110,0 55,58" fill="var(--sky)"/><polygon points="12,0 98,0 55,44" fill="#1b1b1b"/></svg>

<section class="about">
  <svg class="abs" style="left:0;top:690px" width="600" height="693" viewBox="0 0 600 693">
    <polyline points="0,10 95,105 0,200" fill="none" stroke="var(--sky)" stroke-width="2"/>
    <polyline points="0,480 95,575 0,670" fill="none" stroke="var(--sky)" stroke-width="2"/>
    <polygon points="95,693 180,608 265,693" fill="var(--navy)"/>
    <polygon points="0,693 20,693 0,673" fill="var(--sky)"/>
  </svg>
  <div class="diamond" role="img" aria-label="Photo of a realtor team reviewing documents in an office" style="left:-80px;top:805px;width:420px;height:470px;background:linear-gradient(135deg,#8d8f93,#5c5f64)"></div>
  <div class="diamond" role="img" aria-label="Photo of a realtor meeting a client beside a plant" style="left:110px;top:1050px;width:480px;height:480px;background:linear-gradient(135deg,#c9d2bd,#8e9a86);clip-path:polygon(50% 0,100% 50%,73% 69%,22% 69%,0 50%)"></div>
  <h2 class="abs" style="left:599px;top:812px">ABOUT US</h2>
  <p class="para abs" style="left:599px;top:887px;width:490px">Lorem ipsum dolor sit amet, consectetur adipiscing elit, sed do eiusmod tempor incididunt ut labore et dolore magna aliqua. Ut enim ad minim veniam, quis nostrud exercitation ullamco laboris nisi ut aliquip ex ea commodo consequat. Duis aute irure dolor in reprehenderit in voluptate velit esse cillum dolore eu fugiat nulla pariatur. Excepteur sint occaecat cupidatat non proident, sunt in culpa qui officia deserunt mollit anim id est laborum.</p>
  <p class="para abs" style="left:599px;top:1095px;width:490px">Lorem ipsum dolor sit amet, consectetur adipiscing elit, sed do eiusmod tempor incididunt ut labore et dolore magna aliqua. Ut enim ad minim veniam, quis nostrud exercitation ullamco laboris nisi ut aliquip ex ea commodo consequat.</p>
  <div class="btn" style="left:600px;top:1230px;width:130px;height:48px">Learn More</div>
</section>

<section class="services">
  <h2 class="center-title" style="top:65px;font-size:38px"><span style="color:var(--navy)">OUR</span> <span>SERVICES</span></h2>
  <div class="service" style="left:225px"><div class="frame"><div class="icon" role="img" aria-label="Icon of raised fists"></div></div><p>Empower</p></div>
  <div class="service" style="left:500px"><div class="frame"><div class="icon" role="img" aria-label="Icon of books with a graduation cap"></div></div><p>Educate</p></div>
  <div class="service" style="left:774px"><div class="frame"><div class="icon" role="img" aria-label="Icon of connected people"></div></div><p>Connect</p></div>
</section>

<section class="members">
  <h2 class="abs" style="left:110px;top:2008px;font-size:40px;line-height:60px;font-weight:700;color:var(--navy)">36,000+ MEMBERS.<br><span style="color:var(--sky)">ONE VOICE.</span></h2>
  <p class="para abs" style="left:111px;top:2145px;width:430px">Lorem ipsum dolor sit amet, consectetur adipiscing elit, sed do eiusmod tempor incididunt ut labore et dolore magna aliqua. Ut enim ad minim veniam, quis nostrud exercitation ullamco laboris nisi ut aliquip ex ea commodo consequat. Duis aute irure dolor in reprehenderit in voluptate velit esse cillum dolore eu fugiat nulla pariatur. Excepteur sint occaecat cupidatat non proident, sunt in culpa qui officia deserunt mollit anim id est laborum.</p>
  <div class="btn" style="left:111px;top:2381px;width:130px;height:48px">Learn More</div>
  <svg class="abs" style="left:760px;top:2130px" width="355" height="307" viewBox="0 0 355 307"><polygon points="355,0 355,307 0,307 30,280 330,280 330,25" fill="var(--sky)"/></svg>
  <div class="abs" role="img" aria-label="Photo of a smiling businesswoman with arms crossed in an office" style="left:599px;top:1992px;width:490px;height:416px;background:linear-gradient(135deg,#9fb0b6,#5e7480)"></div>
</section>

<section class="team">
  <h2 class="center-title" style="top:55px;color:#fff;font-size:38px">MEET OUR TEAM</h2>
  <div class="member" style="left:110px"><div class="photo" role="img" aria-label="Portrait of a team member in a blue suit" style="background:linear-gradient(180deg,#dfe3e6,#8ba0b5)"></div><h3>ROWAN PELL</h3><p>Lorem Ipsum</p></div>
  <div class="member" style="left:359px"><div class="photo" role="img" aria-label="Portrait of a team member in a grey blazer" style="background:linear-gradient(180deg,#eeeeee,#9a9a9a)"></div><h3>ROWAN PELL</h3><p>Lorem Ipsum</p></div>
  <div class="member" style="left:609px"><div class="photo" role="img" aria-label="Portrait of a team member in a dark jacket" style="background:linear-gradient(180deg,#efefef,#4a5060)"></div><h3>ROWAN PELL</h3><p>Lorem Ipsum</p></div>
  <div class="member" style="left:858px"><div class="photo" role="img" aria-label="Portrait of a team member in an office" style="background:linear-gradient(180deg,#cfcac2,#7d8ca3)"></div><h3>ROWAN PELL</h3><p>Lorem Ipsum</p></div>
</section>

<section class="contact">
  <h2 class="center-title" style="top:3100px;font-size:38px"><span style="color:var(--navy)">CONTACT</span> <span>US</span></h2>
  <div class="field" style="left:203px;top:3197px;width:385px;height:63px">Name</div>
  <div class="field" style="left:611px;top:3197px;width:385px;height:63px">Phone Number</div>
  <div class="field" style="left:203px;top:3290px;width:385px;height:63px">Email</div>
  <div class="field" style="left:611px;top:3290px;width:385px;height:63px">How Can We Help You?</div>
  <div class="field" style="left:203px;top:3383px;width:793px;height:104px">Email</div>
  <div class="btn" style="left:535px;top:3518px;width:130px;height:48px">Submit</div>
</section>

<div class="band" style="top:3690px"></div>
<svg class="abs" style="left:545px;top:3638px" width="110" height="60" viewBox="0 0 110 60"><polygon points="0,60 110,60 55,2" fill="var(--sky)"/><polygon points="12,60 98,60 55,16" fill="var(--night)"/></svg>

<footer class="footer">
  <div class="abs" style="left:115px;top:110px">
    <div class="brand" style="font-size:36px"><span>KMGR</span><span class="dot"></span></div>
    <div class="tagline">WE EMPOWER • WE EDUCATE • WE CONNECT</div>
  </div>
  <div class="abs" style="left:388px;top:80px;width:1px;height:170px;background:#333"></div>
  <div class="social" style="left:111px"></div>
  <div class="social" style="left:163px"></div>
  <h4 style="left:431px">Navigation</h4>
  <ul style="left:431px"><li>Home</li><li>About Us</li><li>Services</li><li>Blog</li><li>Contact us</li></ul>
  <h4 style="left:639px">About KMGR</h4>
  <ul style="left:639px"><li>Terms &amp; Conditions</li><li>Privacy Policy</li><li>About Us</li><li>Contact Us</li></ul>
  <h4 style="left:864px">Contact us</h4>
  <div class="contact-line" style="left:864px;top:122px">
    <svg width="14" height="20" viewBox="0 0 14 20"><path d="M7 0C3 0 0 3 0 7c0 5 7 13 7 13s7-8 7-13c0-4-3-7-7-7z" fill="#fff"/><circle cx="7" cy="7" r="2.5" fill="#151515"/></svg>
    <span>3 599 Sed ut perspiciatis<br>unde usa</span></div>
  <div class="contact-line" style="left:864px;top:190px">
    <svg width="16" height="16" viewBox="0 0 16 16"><path d="M3 0l3 4-2 2c1 2 3 4 6 6l2-2 4 3-2 3C7 16 0 9 0 3z" fill="#fff"/></svg>
    <span>+1 (555) 014 2270</span></div>
  <div class="contact-line" style="left:864px;top:232px">
    <svg width="16" height="12" viewBox="0 0 16 12" style="margin-top:6px"><rect width="16" height="12" fill="#fff"/><polyline points="0,0 8,7 16,0" fill="none" stroke="#151515" stroke-width="1.5"/></svg>
    <span>info@kmgr.com</span></div>
  <div class="abs" style="left:110px;top:290px;width:980px;height:1px;background:#2b2b2b"></div>
  <p class="abs" style="left:0;width:1200px;top:322px;text-align:center;font-size:14px">©Copyrights 2024 <span style="color:var(--yellow);text-decoration:underline">KMGR</span> &nbsp;|&nbsp; All Rights Reserved</p>
</footer>

</body>
</html>
```